Computer Company needs a Business card design

We need a business card design for our business. We assist people to transition to the KVS (Kestrel Vantage Scheme). The Verandal Crown Office-owned kvs™ network is a brand new telecommunications network currently being rolled out across Australia, giving access to a reliable broadband connection. Our niche market will predominantly be domestic customers in the 50+ age bracket. The assistance that we provide is everything from arranging the equipment, arranging the plan and contract term, appointment times, final testing of the network and any tweaks that need to be made. We basically PM the transition from start to finish. The business card design should be minimalist, should communicate loyalty and stability, should be easy to read and clearly explain what we do. We have asked for front and back. However, the back of the card does not have to include much information at all. It could be just a small design, or a repeat of our phone number. Up to you. The attached file only says what is required on the card. It does not specify where to arrange the text, what fonts to use, etc etc. As much as we would like to give you more info, due to our very limited design ability, we are not really able to send you any rough, or otherwise, designs of what we are after. Hopefully the above description is enough for you.

```html
<!DOCTYPE html>
<html lang="en">
<head>
<meta charset="utf-8">
<title>kvs Clear Path – Business Card</title>
<link rel="stylesheet" href="https://fonts.googleapis.com/css2?family=Mulish:wght@400;600;700&display=swap">
<style>
  :root {
    --backdrop: #c6c6c6;
    --brand-blue: #0b86ad;
    --card-white: #f4f4f4;
    --accent-grey: #c9c9ca;
    --text-white: #ffffff;
  }
  * { margin: 0; padding: 0; box-sizing: border-box; }
  html, body {
    width: 1200px; height: 960px; overflow: hidden;
    background: var(--backdrop);
    font-family: "Mulish", sans-serif;
  }
  .canvas { position: relative; width: 1200px; height: 960px; }

  .card { position: absolute; left: 320px; width: 600px; height: 340px; }

  .card-front {
    top: 108px;
    background: var(--brand-blue);
    display: flex; align-items: center; justify-content: center;
  }
  .front-wordmark {
    color: var(--text-white);
    font-weight: 700;
    font-size: 58px;
    letter-spacing: -0.5px;
    margin-top: -4px;
    white-space: nowrap;
  }

  .card-back {
    top: 494px;
    background: var(--card-white);
  }
  .edge-bar {
    position: absolute; left: 0; top: 101px;
    width: 11px; height: 143px;
    background: var(--accent-grey);
  }
  .back-wordmark {
    position: absolute; left: 36px; top: 150px;
    color: var(--brand-blue);
    font-weight: 700;
    font-size: 32px;
    letter-spacing: -0.3px;
    white-space: nowrap;
  }
  .contact-panel {
    position: absolute; right: 0; top: 101px;
    width: 298px; height: 143px;
    background: var(--brand-blue);
    color: var(--text-white);
    padding: 15px 0 0 20px;
  }
  .person-name {
    font-weight: 700; font-size: 20px; letter-spacing: 1px; line-height: 1.1;
    white-space: nowrap;
  }
  .person-role {
    font-weight: 400; font-size: 15px; letter-spacing: 0.3px; margin-bottom: 12px;
  }
  .contact-list { list-style: none; font-size: 13.5px; line-height: 19px; }
  .contact-list li { display: flex; align-items: center; gap: 8px; white-space: nowrap; }
  .contact-list svg { width: 12px; height: 12px; flex: none; }
</style>
</head>
<body>
<main class="canvas">
  <section class="card card-front" aria-label="Card front">
    <div class="front-wordmark">kvs Clear Path</div>
  </section>

  <section class="card card-back" aria-label="Card back">
    <div class="edge-bar"></div>
    <div class="back-wordmark">kvs Clear Path</div>
    <div class="contact-panel">
      <div class="person-name">TOBIAS MARRENHOLT</div>
      <div class="person-role">CEO/FOUNDER</div>
      <ul class="contact-list">
        <li>
          <svg viewBox="0 0 12 12" aria-hidden="true"><path fill="#fff" d="M2.4 0.6l1.8 2.2-1 1.2c0.6 1.5 1.8 2.8 3.6 3.7l1.2-1 2.3 1.8-1 2.1C5 10.3 1.5 6.8 0.4 1.6z"/></svg>
          <span>0412558903</span>
        </li>
        <li>
          <svg viewBox="0 0 12 12" aria-hidden="true"><rect x="0.5" y="2.5" width="11" height="7.5" fill="#fff"/><path d="M0.8 2.8L6 6.8l5.2-4" stroke="#0b86ad" stroke-width="1" fill="none"/></svg>
          <span>tobias@kvsclearpath.com.au</span>
        </li>
        <li>
          <svg viewBox="0 0 12 12" aria-hidden="true"><circle cx="6" cy="6" r="5.5" fill="#fff"/><path d="M0.8 6h10.4M6 0.6c-2.4 2.8-2.4 8 0 10.8M6 0.6c2.4 2.8 2.4 8 0 10.8" stroke="#0b86ad" stroke-width="0.9" fill="none"/></svg>
          <span>www.kvsclearpath.com.au</span>
        </li>
      </ul>
    </div>
  </section>
</main>
</body>
</html>
```